Kesso Tea Premium Matcha brand Label

This is a label design project for a luxury tea brand. Feel free to be creative within the guidelines.
Attached to this project is a document called “Private Label Design Requirements” with the design guidelines and template. There is another document called "Kesso Tea Packaging Instructions" this has more details necessary to stick to the guidelines in the first document.

I have also attached the certifications to be included as well as different variations of the logo for you to use.

If you have any questions, I am here.
Updates

Need extra days to review

Target Market(s)

Young, active, fun, enjoy the finer things

```html
<!DOCTYPE html>
<html lang="en">
<head>
<meta charset="utf-8">
<title>Kesso Tea Premium Organic Ceremonial Matcha Label</title>
<link href="https://fonts.googleapis.com/css2?family=Montserrat:wght@500;600;700;800&display=swap" rel="stylesheet">
<style>
  :root {
    --backdrop: #8d8e92;
    --label-white: #ffffff;
    --label-shade: #efeff0;
    --ink: #141414;
    --matcha: #5cb646;
    --badge-green: #3f8a3a;
    --badge-blue: #2a6fb5;
  }
  * { margin: 0; padding: 0; box-sizing: border-box; }
  html, body {
    width: 1200px; height: 620px; overflow: hidden;
    background: var(--backdrop);
    font-family: "Montserrat", sans-serif;
    color: var(--ink);
  }
  .label {
    position: absolute; left: 30px; top: 199px;
    width: 1140px; height: 222px;
    background: linear-gradient(160deg, var(--label-shade) 0%, var(--label-white) 45%, var(--label-shade) 100%);
    box-shadow: 2px 3px 6px rgba(0,0,0,0.25);
    overflow: hidden;
  }
  .brand {
    position: absolute; left: 0; width: 100%; top: 47px;
    text-align: center;
  }
  .brand__dot {
    display: block; margin: 0 auto 4px;
    width: 32px; height: 32px; border-radius: 50%;
    background: var(--matcha);
  }
  .brand__name { display: block; font-weight: 600; font-size: 11px; line-height: 13px; }
  .product-title {
    position: absolute; left: 389px; top: 104px;
    width: 362px; height: 52px;
    text-align: center;
    font-weight: 800; font-size: 24px; line-height: 26px;
    letter-spacing: 0.3px;
  }
  .product-title__accent { color: var(--matcha); }
  .brackets {
    position: absolute; left: 0; top: 0; width: 1140px; height: 222px;
  }
  .net-weight {
    position: absolute; left: 0; width: 100%; top: 164px;
    text-align: center; font-weight: 600; font-size: 12px; letter-spacing: 0.3px;
  }
  .origin {
    position: absolute; left: 81px; top: 97px;
    font-weight: 600; font-size: 10.5px; line-height: 12.5px;
  }
  .origin__cert { margin-top: 6px; margin-left: -1px; }
  .details {
    position: absolute; left: 865px; top: 50px; width: 250px;
    font-weight: 600; font-size: 8.2px; line-height: 10px;
  }
  .details__heading { font-weight: 700; font-size: 11.5px; line-height: 13px; }
  .details__block + .details__heading { margin-top: 4px; }
  .details__list { list-style: none; }
  .details__list li::before { content: "• "; }
  .certs {
    display: flex; align-items: center; gap: 6px; margin-top: 9px;
  }
  .certs__square { width: 37px; height: 28px; background: var(--badge-blue); border: 2px solid var(--badge-green); }
  .certs__circle { width: 29px; height: 29px; border-radius: 50%; background: var(--badge-green); }
  .certs__note { font-weight: 700; font-size: 8px; line-height: 10px; margin-left: 4px; }
</style>
</head>
<body>
  <div class="label">
    <div class="origin">
      <p>Product of Japan</p>
      <p>Distributed by:</p>
      <p>Kesso Tea Co. | Cedar Falls, Ga</p>
      <p class="origin__cert">Certified Organic by Orvia</p>
    </div>

    <div class="brand">
      <span class="brand__dot"></span>
      <span class="brand__name">Kesso Tea</span>
    </div>

    <svg class="brackets" viewBox="0 0 1140 222" aria-hidden="true">
      <path d="M427 116 H390 V149 H415" fill="none" stroke="#141414" stroke-width="2.5"/>
      <path d="M711 116 H749 V149 H724" fill="none" stroke="#141414" stroke-width="2.5"/>
    </svg>
    <h1 class="product-title">PREMIUM ORGANIC<br>CEREMONIAL <span class="product-title__accent">MATCHA</span></h1>
    <p class="net-weight">Net Wt: 30g</p>

    <div class="details">
      <h2 class="details__heading">Ingredients:</h2>
      <p class="details__block">Premium Organic Japanese Matcha Green Tea</p>
      <h2 class="details__heading">Instructions:</h2>
      <ul class="details__list details__block">
        <li>2 tsp of Matcha</li>
        <li>2oz of Water (170-180 degrees F)</li>
        <li>Whisk in a W formation until frothy</li>
        <li>Sweeten to taste</li>
      </ul>
      <div class="certs">
        <span class="certs__square"></span>
        <span class="certs__circle"></span>
        <p class="certs__note">KEEP REFRIGERATED<br>FOR QUALITY</p>
      </div>
    </div>
  </div>
</body>
</html>
```